Homepage Website Design for luxury picnic company

We need a homepage designed for a luxury picnic business to match our updated branding/logo which we're currently completing on PixelHarbor with another competition. Please see attached logo/colour example to use for now.

PLEASE NOTE: We are only after graphic design concepts as part of this competition. I will get another developer to actually code the website.

It is important that this website is very elegant/luxurious and stands out from a visual perspective. The images really need to match the content/sections also. The new branding colours are silver with a dark background. Please create the new website homepage to match these colours/branding.

Please create as many concepts as possible and then I will provide feedback from there

The website content including sections is here https://files.quorvanta.com/doc/d/7kRmWp2QxLn9TfBv4ZsYh3JcA8eGuD5oNiKtE1rVbXq/view?mode=share

Images to use are located here https://store.quorvanta.com/vault/folders/9HwTnK4-MzPa2RbE73-VyxLqJdsfGoUe?mode=share and there is also lots of videos at this link which you can screenshot images out of if needed https://www.boxtelmo.net/sh/k827rvwd3mjq8t2/ZZQmnx4RtUe7hWLP9C5dvkXbN?dl=0

Any questions please contact me

1 page

```html
<!DOCTYPE html>
<html lang="en">
<head>
<meta charset="utf-8">
<title>Luxury Picnics – Homepage</title>
<link rel="stylesheet" href="https://fonts.googleapis.com/css2?family=Cormorant+Garamond:wght@400;500&family=Crimson+Pro:wght@400;500&family=Hind:wght@400&display=swap">
<style>
  :root{
    --night:#0a0d1a;
    --silver:#c9cad1;
    --silver-soft:#9a9cab;
    --white:#ffffff;
    --mist:#f4f4f4;
    --stone:#a9a9ad;
    --ink:#2b2b2f;
    --line:#cfcfd3;
    --gold:#f2d31b;
  }
  *{box-sizing:border-box;margin:0;padding:0}
  h1,h2,h3,p{font-weight:400}
  html,body{width:1200px;height:3356px;overflow:hidden;background:var(--white)}
  body{position:relative;font-family:"Crimson Pro",Georgia,serif;color:var(--ink)}
  .night{position:absolute;left:0;top:0;width:1200px;height:1467px;background:var(--night)}
  .rule{position:absolute;height:1px;width:75px;background:var(--silver-soft)}
  .label{position:absolute;font-family:"Cormorant Garamond",Georgia,serif;font-size:20px;letter-spacing:6px;text-transform:uppercase;color:var(--silver);white-space:nowrap}
  .label.light{color:var(--stone)}
  .step-num{position:absolute;left:112px;width:76px;height:76px;border:1px solid var(--silver);border-radius:50%;color:var(--white);font-size:24px;display:flex;align-items:center;justify-content:center}
  .step-link{position:absolute;left:150px;width:0;border-left:1px dashed var(--silver-soft)}
  .step-title{position:absolute;left:262px;color:var(--white);font-size:15px;white-space:nowrap}
  .step-body{position:absolute;left:262px;width:820px;color:var(--silver-soft);font-size:11.5px;line-height:30px}
  .step-body.sans{font-family:"Hind",Arial,sans-serif;font-size:10px;line-height:22px}
  .btn{position:absolute;display:flex;align-items:center;justify-content:center;font-family:"Crimson Pro",Georgia,serif;font-size:11px;letter-spacing:1px;text-transform:uppercase;white-space:nowrap}
  .btn.on-dark{border:1px solid var(--silver);color:var(--silver)}
  .btn.on-light{border:1px solid var(--ink);color:var(--ink)}
  .photo{position:absolute}
  .spots-heading{position:absolute;left:360px;top:872px;width:500px;color:var(--white);font-size:38px;line-height:54px}
  .spots-body{position:absolute;left:360px;top:1066px;width:480px;color:var(--white);font-family:"Hind",Arial,sans-serif;font-size:9.5px;line-height:22.5px}
  .spots-body p+p{margin-top:22px}
  .place-title{position:absolute;color:var(--stone);font-size:39px;line-height:54px;white-space:nowrap}
  .play{position:absolute;width:78px;height:78px}
  .note{position:absolute;left:0;top:2593px;width:1200px;height:111px;background:var(--mist)}
  .note p{position:absolute;left:262px;top:28px;width:676px;text-align:center;font-size:14px;line-height:18px;color:var(--ink)}
  .card{position:absolute;top:2855px;width:314px;height:336px;background:var(--mist);border:1px solid var(--line)}
  .quote-mark{position:absolute;left:0;top:26px;width:100%;text-align:center;font-size:96px;line-height:1;color:var(--ink);font-weight:500}
  .quote-text{position:absolute;left:24px;top:110px;width:266px;text-align:center;font-family:"Hind",Arial,sans-serif;font-size:11px;line-height:18px;color:var(--ink)}
  .stars{position:absolute;left:0;top:246px;width:100%;display:flex;justify-content:center}
  .avatar{position:absolute;left:119px;top:298px;width:76px;height:76px;border-radius:50%;background:radial-gradient(circle at 50% 45%,#6a5a48,#2a241f)}
  .name{position:absolute;width:314px;text-align:center;font-family:"Cormorant Garamond",Georgia,serif;letter-spacing:5px;text-transform:uppercase;color:var(--stone);font-size:16px}
  .date{position:absolute;width:314px;text-align:center;font-size:11px;letter-spacing:3px;color:var(--ink)}
</style>
</head>
<body>

<section class="night" aria-label="How our picnics work and picnic spots">
  <div class="rule" style="left:112px;top:78px"></div>
  <h2 class="label" style="left:112px;top:95px">How our picnics work</h2>

  <div class="step-num" style="top:153px">01</div>
  <div class="step-link" style="top:231px;height:66px"></div>
  <div class="step-num" style="top:298px">02</div>
  <div class="step-link" style="top:376px;height:68px"></div>
  <div class="step-num" style="top:445px">03</div>

  <h3 class="step-title" style="top:181px">Receive an Email</h3>
  <p class="step-body" style="top:209px">We then email you all the important information in the lead up to your picnic. You can also select your food, beverages and chalkboard message quickly and easily via our website. We’re also available to answer any queries you may have.</p>

  <h3 class="step-title" style="top:325px">Discover Stunning Picnic Spot</h3>
  <p class="step-body" style="top:355px">Discover your stunning picnic spot where your picnic setting will be set up waiting for you. We say a quick hello before leaving you to enjoy the experience. We provide your choice of still or sparkling water chilled on ice for every picnic and will also deliver your food and drinks if you choose the catered option.</p>

  <h3 class="step-title" style="top:464px">Checkout our&nbsp; Packages and Locations</h3>
  <p class="step-body sans" style="top:498px">You can see our packages, locations we offer and each of their available dates and times via our website. When you’re ready you can book a picnic via our website and select your type of picnic and location including date and time. To secure your booking you either need to pay in full or put down a &nbsp;$100+ GST deposit with payment plan options available at no extra cost.</p>

  <div class="btn on-dark" style="left:469px;top:575px;width:262px;height:45px">Book your picnic</div>

  <div class="photo" role="img" aria-label="Picnic setting with cushions and rugs beside a bare tree overlooking a mountain valley" style="left:0;top:646px;width:450px;height:601px;background:linear-gradient(160deg,#6c7285 0%,#4a5064 40%,#383a4a 70%,#5a4a55 100%)"></div>
  <div class="photo" role="img" aria-label="Woven picnic basket and patterned cushions on a red rug at a cliff edge" style="left:827px;top:792px;width:373px;height:600px;background:linear-gradient(170deg,#3b4168 0%,#3a3d58 45%,#5a4a4e 75%,#6b4a4a 100%)"></div>

  <div class="rule" style="left:486px;top:770px"></div>
  <h2 class="label" style="left:486px;top:788px">Picnic spots</h2>

  <h3 class="spots-heading">You will love our<br>breathtaking locations which<br>you can’t find on Findora!</h3>
  <div class="spots-body">
    <p>We have handpicked the absolute best picnic spots in the Blue Mountains from years of local knowledge. They’re all accessible with regular vehicles and only a short walk from where you park. Our spots are very quiet giving you a peaceful and unique glimpse of the Blue Mountains.</p>
    <p>Some spots do have waist high ledges you need to step down to access the location. While we currently do not cater for wheelchair access or other similar disabilities, this is a priority for us and we will add on some more accessible spots in the near future. Please contact us if you would like any further information.</p>
  </div>
</section>

<h3 class="place-title" style="left:112px;top:1667px">Wentworth Falls<br>&nbsp;Picnic Spot</h3>
<div class="btn on-light" style="left:112px;top:1810px;width:262px;height:44px">View available dates &amp; times</div>
<div class="photo" role="img" aria-label="Video still: guests seated on cushions at a clifftop picnic under a cloudy sky" style="left:487px;top:1543px;width:600px;height:449px;background:linear-gradient(175deg,#6d7387 0%,#4f5568 40%,#3a3a44 65%,#7a2d35 100%)"></div>
<svg class="play" style="left:748px;top:1728px" viewBox="0 0 78 78" aria-hidden="true"><circle cx="39" cy="39" r="37" fill="none" stroke="#fff" stroke-width="2"/><path d="M30 23 L56 39 L30 55 Z" fill="none" stroke="#fff" stroke-width="2.5" stroke-linejoin="round"/></svg>

<div class="photo" role="img" aria-label="Video still: guests seated on cushions at a clifftop picnic under a cloudy sky" style="left:112px;top:2068px;width:601px;height:449px;background:linear-gradient(175deg,#6d7387 0%,#4f5568 40%,#3a3a44 65%,#7a2d35 100%)"></div>
<svg class="play" style="left:374px;top:2253px" viewBox="0 0 78 78" aria-hidden="true"><circle cx="39" cy="39" r="37" fill="none" stroke="#fff" stroke-width="2"/><path d="M30 23 L56 39 L30 55 Z" fill="none" stroke="#fff" stroke-width="2.5" stroke-linejoin="round"/></svg>
<h3 class="place-title" style="left:826px;top:2193px">Katoomba<br>&nbsp;Picnic Spot</h3>
<div class="btn on-light" style="left:826px;top:2336px;width:262px;height:44px">View available dates &amp; times</div>

<div class="note"><p>IMPORTANT NOTE: We don’t publicly advertise our exact locations so we can continue to keep them a secret. For this reason we provide our clients with the directions the day prior to the picnic and ask that you do not share the exact location!</p></div>

<div class="rule" style="left:112px;top:2779px"></div>
<h2 class="label light" style="left:112px;top:2797px">Testimonials</h2>

<svg width="0" height="0" style="position:absolute" aria-hidden="true"><defs><path id="star" d="M7 0l2 4.6 5 .4-3.8 3.2 1.2 4.8L7 10.4 2.6 13l1.2-4.8L0 5l5-.4z"/></defs></svg>

<article class="card" style="left:112px">
  <div class="quote-mark">“</div>
  <p class="quote-text">Lorem ipsum dolor sit amet, consectetur adipiscing elit, sed do eiusmod tempor incididunt ut labore et dolore magna aliqua. Quis ipsum suspendisse ultrices gravida. Risus commodo viverra maecenas accumsan lacus vel facilisis.</p>
  <div class="stars"><svg width="96" height="14" viewBox="0 0 96 14" aria-label="Five stars"><g fill="var(--gold)"><use href="#star"/><use href="#star" x="20"/><use href="#star" x="41"/><use href="#star" x="61"/><use href="#star" x="82"/></g></svg></div>
  <div class="avatar" role="img" aria-label="Customer portrait"></div>
</article>
<article class="card" style="left:443px">
  <div class="quote-mark">“</div>
  <p class="quote-text">Lorem ipsum dolor sit amet, consectetur adipiscing elit, sed do eiusmod tempor incididunt ut labore et dolore magna aliqua. Quis ipsum suspendisse ultrices gravida. Risus commodo viverra maecenas accumsan lacus vel facilisis.</p>
  <div class="stars"><svg width="96" height="14" viewBox="0 0 96 14" aria-label="Five stars"><g fill="var(--gold)"><use href="#star"/><use href="#star" x="20"/><use href="#star" x="41"/><use href="#star" x="61"/><use href="#star" x="82"/></g></svg></div>
  <div class="avatar" role="img" aria-label="Customer portrait"></div>
</article>
<article class="card" style="left:773px">
  <div class="quote-mark">“</div>
  <p class="quote-text">Lorem ipsum dolor sit amet, consectetur adipiscing elit, sed do eiusmod tempor incididunt ut labore et dolore magna aliqua. Quis ipsum suspendisse ultrices gravida. Risus commodo viverra maecenas accumsan lacus vel facilisis.</p>
  <div class="stars"><svg width="96" height="14" viewBox="0 0 96 14" aria-label="Five stars"><g fill="var(--gold)"><use href="#star"/><use href="#star" x="20"/><use href="#star" x="41"/><use href="#star" x="61"/><use href="#star" x="82"/></g></svg></div>
  <div class="avatar" role="img" aria-label="Customer portrait"></div>
</article>

<div class="name" style="left:112px;top:3245px">Jane Doe</div>
<div class="date" style="left:112px;top:3266px">11/17/2020</div>
<div class="name" style="left:443px;top:3245px">Jane Doe</div>
<div class="date" style="left:443px;top:3266px">11/17/2020</div>
<div class="name" style="left:773px;top:3245px">Jane Doe</div>
<div class="date" style="left:773px;top:3266px">11/17/2020</div>

</body>
</html>
```